Business Card Design Project

We have 2 businesses which help each other.

Brightvale Care (providing nurses to hospitals/nursing homes etc)

and

Brightvale HR (providing nurses to our brightvale care business - but also providing workers for farms, restaurants meatworks etc)

We would like 2 separate business cards - but similar design and feel

Target Market(s)

Managers of nursing homes, hospitals, farms, meatworks, restauants

Industry/Entity Type

Business

Requirements
Must have
• both logos
https://www.filequay-example.com/s/6v4i7j2fzkpw8wx/BrightvaleHR-Logo-Horizontal.ai
https://www.filequay-example.com/s/dr33nlhq82w3z6t/46051_844932_40145_sourcefile.ai

You may edit the layout of Brightvale HR logo

Name
position
mobile
Phone
name@brightvalehr.com.au
brigthvalehr.com.au

Name
position
mobile
phone
name@brightvalecare.net.au
brightvalecare.net.au

```html
<!DOCTYPE html>
<html lang="en">
<head>
<meta charset="utf-8">
<title>Brightvale Care – Business Card</title>
<link rel="stylesheet" href="https://fonts.googleapis.com/css2?family=Open+Sans:wght@400;700;800&display=swap">
<style>
  :root {
    --ink-indigo: #2e3192;
    --sky-blue: #29a8e0;
    --deep-blue: #0e4c96;
    --paper: #ffffff;
  }
  html, body {
    margin: 0;
    padding: 0;
    overflow: hidden;
    background: var(--paper);
  }
  .card {
    position: relative;
    width: 686px;
    height: 1200px;
    overflow: hidden;
    background: var(--paper);
    font-family: "Open Sans", sans-serif;
  }
  .card__waves {
    position: absolute;
    inset: 0;
  }
  .brand-mark {
    position: absolute;
    left: 416px;
    top: 128px;
    width: 80px;
    height: 80px;
    border-radius: 50%;
    background: var(--sky-blue);
  }
  .brand-name {
    position: absolute;
    left: 100px;
    top: 216px;
    margin: 0;
    font-size: 66px;
    font-weight: 800;
    line-height: 1;
    letter-spacing: -1.5px;
    color: var(--ink-indigo);
    white-space: nowrap;
  }
  .text {
    position: absolute;
    left: 48px;
    margin: 0;
    line-height: 1;
    color: var(--paper);
    white-space: nowrap;
  }
  .person-name {
    top: 710px;
    font-size: 52px;
    font-weight: 700;
    letter-spacing: -1px;
  }
  .person-role {
    top: 774px;
    font-size: 29px;
    font-weight: 400;
  }
  .contact {
    top: 861px;
    font-size: 30px;
    font-weight: 400;
  }
  .contact__row {
    display: flex;
    height: 44px;
  }
  .contact__label {
    width: 127px;
  }
  .divider {
    position: absolute;
    left: 34px;
    top: 1063px;
    width: 600px;
    height: 4px;
    background: var(--paper);
  }
  .website {
    left: 122px;
    top: 1089px;
    font-size: 40px;
    font-weight: 400;
  }
</style>
</head>
<body>
  <div class="card">
    <svg class="card__waves" width="686" height="1200" viewBox="0 0 686 1200" aria-hidden="true">
      <path d="M0,512 Q430,540 686,790 L686,1200 L0,1200 Z" fill="var(--deep-blue)"/>
      <path d="M0,532 Q420,562 686,812 L686,1200 L0,1200 Z" fill="var(--sky-blue)"/>
    </svg>

    <div class="brand-mark" aria-hidden="true"></div>
    <p class="brand-name">Brightvale Care</p>

    <p class="text person-name">First Lastname</p>
    <p class="text person-role">executive of business cards</p>

    <div class="text contact">
      <div class="contact__row">first.lastname@brightvalehr.com.au</div>
      <div class="contact__row"><span class="contact__label">mobile:</span><span>0491 570 156</span></div>
      <div class="contact__row"><span class="contact__label">phone:</span><span>0491 570 157</span></div>
    </div>

    <div class="divider"></div>
    <p class="text website">brightvalehr.com.au</p>
  </div>
</body>
</html>
```